Merrow Trade finance web design

We are a newly established business which provides invoice finance to Small Businesses in England and Wales.
Our approach is very much a funder where the small business owner can talk to the decision maker. We will guarantee on receipt of information, a decision within 24 hours.
We are not a bank so the look of the website need to be friendly but professional.
Have two types of people we are trying to attract to the website: 1) partners who are small business owners and 2) introducers who is accountants and commercial brokers who introduce us to the small businesses.
Currently no website, although domain has been reserved.
The design should be:
Professional
“Clean” Look
Designed to convey Trust and Authority.
Appeal to the small business owner.
Must incorporate:
Logo (attached)
Front page:Top tabs to other pages 1) About us 2) Services 3) Introducers 4) Contact us
Need picture and logo on page.
1) About us page- Room for talk about the company, the people and our critera.
2) Services page- We need for what invoice finance is, and 5 boxes for different services we will provide. (link on page to contact us)
3) Introducers page- We need a part for why become an introducer? Who we can help? Why we are different? (link on page to contact us)
4) Contact us page- Office address, email, tel and if possible a map and a contact me part which will email direct to us.
Text will be provided for the design, if we can see the setup of the website we will provide a part for each of the pages to support.
Styles we think convey the correct image:
www.dornelcapital.example
www.plivanlend.example
www.quorbacredit.example
Target Market(s)
Small business owners
Industry/Entity Type
Finance
Number of Pages Required
5+ page
Look and feel

```html
<!DOCTYPE html>
<html lang="en">
<head>
<meta charset="utf-8">
<title>Merrow Trade finance</title>
<link href="https://fonts.googleapis.com/css2?family=Raleway:wght@400;600;700&family=Open+Sans:ital,wght@0,400;0,600;0,700;1,400&display=swap" rel="stylesheet">
<style>
:root{
  --red:#c8102e;
  --red-dark:#a80d25;
  --red-soft:#d4505f;
  --ink:#222;
  --text:#555;
  --muted:#888;
  --grey-bg:#f1f1f1;
  --footer:#1d1d1d;
  --white:#fff;
}
*{margin:0;padding:0;box-sizing:border-box}
html,body{width:1200px;height:2723px;overflow:hidden;background:var(--white)}
body{position:relative;font-family:'Open Sans',Arial,sans-serif;color:var(--text)}
.section{position:absolute;left:0;width:1200px}
h2{font-family:'Raleway',Arial,sans-serif;font-weight:600;color:var(--ink);font-size:27px;text-align:center;position:absolute;left:0;width:1200px}

/* header */
.site-header{top:0;height:82px;border-top:5px solid var(--red);background:var(--white)}
.brand{position:absolute;left:100px;top:14px;display:flex;align-items:center;gap:10px}
.brand-mark{width:22px;height:22px;border-radius:50%;background:var(--red)}
.brand-name{font-family:'Raleway',Arial,sans-serif;font-weight:700;font-size:26px;color:var(--ink);line-height:1.1}
.brand-sub{position:absolute;left:132px;top:50px;font-family:'Raleway',Arial,sans-serif;font-weight:700;font-size:10px;letter-spacing:1px;color:var(--red)}
.main-nav{position:absolute;right:100px;top:30px;display:flex;gap:36px;font-family:'Raleway',Arial,sans-serif;font-weight:600;font-size:16px;color:var(--ink);align-items:center}
.main-nav .active{color:var(--red)}

/* hero */
.hero{top:82px;height:426px;background:linear-gradient(100deg,#4a4540 0%,#8d8a87 45%,#c9c8c7 75%,#e7e5e3 100%)}
.hero-photo{position:absolute;inset:0}
.hero-shade{position:absolute;inset:0;background:rgba(0,0,0,.25)}
.hero-title{position:absolute;top:120px;left:0;width:1200px;text-align:center;font-family:'Raleway',Arial,sans-serif;font-weight:700;font-size:64px;color:var(--white)}
.hero-sub{position:absolute;top:200px;left:0;width:1200px;text-align:center;font-size:20px;color:var(--white)}
.signup{position:absolute;top:248px;left:260px;display:flex}
.signup-input{width:532px;height:46px;background:var(--white);font-size:13px;color:#999;padding:14px 22px}
.signup-btn{width:149px;height:46px;background:var(--red);color:var(--white);font-weight:700;font-size:14px;text-align:center;line-height:46px}
.hero-dots{position:absolute;top:376px;left:542px;display:flex;gap:4px}
.hero-dots span{width:26px;height:5px;background:var(--white);border-radius:3px}
.hero-dots span:first-child{background:var(--red)}

/* welcome */
.welcome{top:508px;height:362px}
.welcome h2{top:40px}
.welcome-text{position:absolute;top:86px;left:200px;width:800px;text-align:center;font-size:12px;line-height:24px;color:var(--muted)}
.features{position:absolute;top:156px;left:100px;display:flex}
.feature{width:200px;height:154px;color:var(--white);text-align:center;font-family:'Raleway',Arial,sans-serif;font-weight:700;font-size:16px;padding-top:24px}
.feature svg{display:block;margin:0 auto 24px}
.f1{background:#d25a66}.f2{background:#cf3f4e}.f3{background:#cc2a3c}.f4{background:#c81e32}.f5{background:#c5142a}

/* how it works */
.how{top:870px;height:323px;background:var(--grey-bg)}
.how h2{top:40px}
.step{position:absolute;top:110px;width:280px;text-align:center}
.step-circle{position:relative;width:146px;height:146px;margin:0 auto;border:4px solid var(--ink);border-radius:50%;background:var(--white);display:flex;align-items:center;justify-content:center}
.step-num{position:absolute;right:-6px;top:2px;width:38px;height:38px;border-radius:50%;background:#333;color:var(--white);font-weight:700;font-size:18px;line-height:38px;text-align:center}
.step-label{margin-top:16px;font-family:'Raleway',Arial,sans-serif;font-weight:600;font-size:17px;color:var(--ink)}
.step-arrow{position:absolute;top:176px}

/* services */
.services{top:1193px;height:387px;background:linear-gradient(90deg,#4b4b4b,#6c6c6c 50%,#545454)}
.services h2{top:32px;color:var(--white)}
.service{position:absolute;top:90px;width:237px;height:257px;box-shadow:0 4px 10px rgba(0,0,0,.35)}
.service-photo{height:217px}
.service-label{height:40px;background:var(--red);color:var(--white);font-weight:700;font-size:14px;letter-spacing:.5px;text-align:center;line-height:40px}

/* why choose */
.why{top:1580px;height:377px}
.why-image{position:absolute;left:65px;top:48px;width:535px;height:292px;background:linear-gradient(180deg,#eceef0 0%,#d9dbde 70%,#9a9c9f 100%)}
.why-title{position:absolute;left:645px;top:50px;font-family:'Raleway',Arial,sans-serif;font-weight:600;font-size:27px;color:var(--ink)}
.why-list{position:absolute;left:645px;top:108px;list-style:none;font-size:12px;color:#666}
.why-list li{height:37px;display:flex;align-items:flex-start;gap:12px}
.read-more{position:absolute;left:645px;top:307px;font-weight:700;font-size:12px;color:var(--red)}

/* testimonials */
.testimonials{top:1957px;height:243px;background:linear-gradient(90deg,#b8102a,#c8102e 50%,#b30e27)}
.testimonials h2{top:32px;color:var(--white);font-size:26px}
.quote-badge{position:absolute;left:105px;top:84px;width:145px;height:112px;border-radius:56px;background:var(--white)}
.quote-mark{position:absolute;left:120px;top:100px;font-family:Georgia,serif;font-size:110px;line-height:100px;color:#ddd}
.client-photo{position:absolute;left:188px;top:78px;width:112px;height:112px;border-radius:50%;background:linear-gradient(160deg,#e9e9e9,#b7bac0);border:4px solid var(--white)}
.quote-text{position:absolute;left:318px;top:82px;width:780px;font-style:italic;font-size:13px;line-height:24px;color:var(--white)}
.client-name{position:absolute;left:318px;top:170px;font-weight:700;font-size:14px;color:var(--white)}
.t-dots{position:absolute;left:570px;top:184px;display:flex;gap:3px}
.t-dots span{width:16px;height:16px;border-radius:50%;border:2px solid var(--white)}
.t-dots span:first-child{background:var(--white)}

/* introducers */
.introducers{top:2200px;height:223px}
.introducers h2{top:40px}
.partner{position:absolute;top:88px;width:156px;height:82px;border:1px solid #ddd;display:flex;align-items:center;justify-content:center}
.partner span{width:100px;height:30px;border-radius:4px;background:#e3e6ea}
.carousel-arrow{position:absolute;top:116px}

/* footer */
.site-footer{top:2423px;height:300px;background:var(--footer);color:#ccc}
.footer-brand{position:absolute;left:100px;top:70px;display:flex;align-items:center;gap:14px}
.footer-brand .brand-mark{width:30px;height:30px;background:var(--white)}
.footer-brand .brand-name{color:var(--white);font-size:34px}
.footer-sub{position:absolute;left:144px;top:118px;font-family:'Raleway',Arial,sans-serif;font-weight:700;font-size:12px;letter-spacing:1px;color:var(--white)}
.footer-col{position:absolute;top:42px}
.footer-col h3{font-family:'Raleway',Arial,sans-serif;font-weight:700;font-size:16px;color:var(--white);margin-bottom:18px}
.footer-links{list-style:none;font-size:12px;line-height:27px;color:#ddd}
.news-text{font-size:12px;line-height:20px;width:250px}
.news-input{margin-top:12px;width:244px;height:34px;background:var(--white);color:#999;font-size:11px;padding:10px 14px}
.news-btn{margin-top:14px;display:inline-block;border:1px solid var(--white);border-radius:3px;padding:8px 14px;font-weight:700;font-size:11px;color:var(--white)}
.contact-row{display:flex;gap:24px;font-size:12px;line-height:18px;color:#ddd;margin-bottom:16px}
.contact-row svg{flex:none;margin-top:2px}
.footer-rule{position:absolute;left:100px;top:234px;width:1000px;height:1px;background:#333}
.copyright{position:absolute;left:100px;top:260px;font-size:11px;color:#ccc}
.social{position:absolute;left:958px;top:250px;display:flex;gap:7px}
.social span{width:31px;height:31px;border:2px solid var(--white);border-radius:50%}
</style>
</head>
<body>

<header class="section site-header">
  <div class="brand"><span class="brand-mark"></span><span class="brand-name">Merrow Trade finance</span></div>
  <div class="brand-sub">MERROW TRADE FINANCE LIMITED</div>
  <nav class="main-nav">
    <span class="active">Home</span><span>About us</span><span>Services</span><span>Introducers</span><span>Contact us</span>
    <svg width="16" height="16" viewBox="0 0 16 16"><circle cx="6.5" cy="6.5" r="5" fill="none" stroke="#222" stroke-width="2"/><line x1="10.5" y1="10.5" x2="15" y2="15" stroke="#222" stroke-width="2.4"/></svg>
  </nav>
</header>

<section class="section hero">
  <div class="hero-photo" role="img" aria-label="Photo of a person working on a laptop showing a paid invoice"></div>
  <div class="hero-shade"></div>
  <h1 class="hero-title">Merrow Trade finance</h1>
  <p class="hero-sub">We are a new business which provides invoice finance to Small Businesses in England and Wales.</p>
  <div class="signup"><div class="signup-input">EMAIL ADDRESS</div><div class="signup-btn">GET STARTED</div></div>
  <div class="hero-dots"><span></span><span></span><span></span><span></span></div>
</section>

<section class="section welcome">
  <h2>Welcome to Merrow Trade finance</h2>
  <p class="welcome-text">At vero eos et accusamus et iusto odio dignissimos ducimus qui blanditiis praesentium voluptatum deleniti atque corrupti quos dolores et quas molestias excepturi sint occaecati cupiditate non provident, similique sunt in culpa qui officia deserunt mollitia</p>
  <div class="features">
    <div class="feature f1"><svg width="52" height="52" viewBox="0 0 52 52"><rect x="4" y="22" width="10" height="26" fill="#fff"/><path d="M18 24 L28 6 Q34 6 33 14 L31 22 H46 Q50 24 48 30 L44 46 Q42 48 38 48 H18 Z" fill="#fff"/></svg>Fast Approval</div>
    <div class="feature f2"><svg width="52" height="52" viewBox="0 0 52 52"><path d="M26 4 L50 48 H2 Z" fill="#fff"/><rect x="23.5" y="18" width="5" height="16" fill="#cf3f4e"/><rect x="23.5" y="38" width="5" height="5" fill="#cf3f4e"/></svg>Risk Assessment</div>
    <div class="feature f3"><svg width="52" height="52" viewBox="0 0 52 52"><path d="M48 4 L4 24 L20 30 L26 48 Z M20 30 L48 4" fill="#fff" stroke="#cc2a3c" stroke-width="2"/></svg>High Limits</div>
    <div class="feature f4"><svg width="52" height="52" viewBox="0 0 52 52" fill="#fff"><path d="M4 4H20L14 10L22 18L18 22L10 14L4 20Z"/><path d="M48 4V20L42 14L34 22L30 18L38 10L32 4Z"/><path d="M4 48V32L10 38L18 30L22 34L14 42L20 48Z"/><path d="M48 48H32L38 42L30 34L34 30L42 38L48 32Z"/></svg>Flexible Finance</div>
    <div class="feature f5"><svg width="52" height="52" viewBox="0 0 52 52"><path d="M16 24V16A10 10 0 0 1 36 16V24" fill="none" stroke="#fff" stroke-width="5"/><rect x="10" y="24" width="32" height="24" rx="3" fill="#fff"/></svg>Safe, Secure, Trusted</div>
  </div>
</section>

<section class="section how">
  <h2>How It Works</h2>
  <div class="step" style="left:32px"><div class="step-circle"><svg width="60" height="44" viewBox="0 0 60 44"><rect x="10" y="4" width="40" height="28" rx="2" fill="none" stroke="#c8102e" stroke-width="4"/><rect x="2" y="35" width="56" height="5" rx="2" fill="#c8102e"/></svg><span class="step-num">1</span></div><div class="step-label">Apply online</div></div>
  <svg class="step-arrow" style="left:240px" width="84" height="16" viewBox="0 0 84 16"><line x1="0" y1="8" x2="78" y2="8" stroke="#333" stroke-width="3"/><path d="M70 1 L80 8 L70 15" fill="none" stroke="#333" stroke-width="3"/></svg>
  <div class="step" style="left:311px"><div class="step-circle"><svg width="64" height="50" viewBox="0 0 64 50" fill="#c8102e"><circle cx="14" cy="12" r="7"/><circle cx="50" cy="12" r="7"/><circle cx="32" cy="14" r="9"/><path d="M2 40Q2 24 14 24Q22 24 24 30V40Z"/><path d="M62 40Q62 24 50 24Q42 24 40 30V40Z"/><path d="M18 48Q18 28 32 28Q46 28 46 48Z"/></svg><span class="step-num">2</span></div><div class="step-label">Add a customer</div></div>
  <svg class="step-arrow" style="left:520px" width="84" height="16" viewBox="0 0 84 16"><line x1="0" y1="8" x2="78" y2="8" stroke="#333" stroke-width="3"/><path d="M70 1 L80 8 L70 15" fill="none" stroke="#333" stroke-width="3"/></svg>
  <div class="step" style="left:591px"><div class="step-circle"><svg width="56" height="54" viewBox="0 0 56 54" fill="#c8102e"><path d="M28 2L44 18H34V32H22V18H12Z"/><rect x="4" y="36" width="48" height="16" rx="3"/><circle cx="38" cy="44" r="2.5" fill="#fff"/><circle cx="45" cy="44" r="2.5" fill="#fff"/></svg><span class="step-num">3</span></div><div class="step-label">Upload your invoice</div></div>
  <svg class="step-arrow" style="left:800px" width="84" height="16" viewBox="0 0 84 16"><line x1="0" y1="8" x2="78" y2="8" stroke="#333" stroke-width="3"/><path d="M70 1 L80 8 L70 15" fill="none" stroke="#333" stroke-width="3"/></svg>
  <div class="step" style="left:871px"><div class="step-circle"><svg width="60" height="60" viewBox="0 0 60 60"><circle cx="30" cy="30" r="28" fill="#c8102e"/><path d="M17 30L26 39L44 21" fill="none" stroke="#fff" stroke-width="7"/></svg><span class="step-num">4</span></div><div class="step-label">Verify and get funded</div></div>
</section>

<section class="section services">
  <h2>Our Services</h2>
  <div class="service" style="left:100px"><div class="service-photo" role="img" aria-label="Photo of hands with a pen and calculator over paperwork" style="background:linear-gradient(135deg,#e8e4df,#b9b1a8)"></div><div class="service-label">INVOICE FINANCING</div></div>
  <div class="service" style="left:355px"><div class="service-photo" role="img" aria-label="Photo of hands typing on a laptop with a spreadsheet" style="background:linear-gradient(135deg,#dfe2e6,#8f9499)"></div><div class="service-label">INVOICE FACTORING</div></div>
  <div class="service" style="left:609px"><div class="service-photo" role="img" aria-label="Photo of a hand holding a payment card over a tablet" style="background:linear-gradient(135deg,#e9e6e2,#a39b93)"></div><div class="service-label">ASSET FINANCE</div></div>
  <div class="service" style="left:864px"><div class="service-photo" role="img" aria-label="Photo of a smiling small business owner in a cafe" style="background:linear-gradient(135deg,#8a6f5a,#d8cfc6)"></div><div class="service-label">INVOICE DISCOUNTING</div></div>
</section>

<section class="section why">
  <div class="why-image" role="img" aria-label="Image of a laptop showing website code in a browser inspector"></div>
  <div class="why-title">Why Choose Merrow Trade finance</div>
  <ul class="why-list">
    <li><svg width="14" height="14" viewBox="0 0 14 14"><circle cx="7" cy="7" r="7" fill="#c8102e"/><path d="M3.5 7L6 9.5L10.5 4.5" fill="none" stroke="#fff" stroke-width="2"/></svg>On the other hand, we denounce with righteous indignation and dislike.</li>
    <li><svg width="14" height="14" viewBox="0 0 14 14"><circle cx="7" cy="7" r="7" fill="#c8102e"/><path d="M3.5 7L6 9.5L10.5 4.5" fill="none" stroke="#fff" stroke-width="2"/></svg>At vero eos et accusamus et iusto odio dignissimos ducimus qui blanditiis.</li>
    <li><svg width="14" height="14" viewBox="0 0 14 14"><circle cx="7" cy="7" r="7" fill="#c8102e"/><path d="M3.5 7L6 9.5L10.5 4.5" fill="none" stroke="#fff" stroke-width="2"/></svg>Certain circumstances and owing to the claims of duty or the oblig</li>
    <li><svg width="14" height="14" viewBox="0 0 14 14"><circle cx="7" cy="7" r="7" fill="#c8102e"/><path d="M3.5 7L6 9.5L10.5 4.5" fill="none" stroke="#fff" stroke-width="2"/></svg>On the other hand, we denounce with righteous indignation and dislike.</li>
    <li><svg width="14" height="14" viewBox="0 0 14 14"><circle cx="7" cy="7" r="7" fill="#c8102e"/><path d="M3.5 7L6 9.5L10.5 4.5" fill="none" stroke="#fff" stroke-width="2"/></svg>Nemo enim ipsam voluptatem quia voluptas sit aspernatur aut odit aut fugit,</li>
  </ul>
  <div class="read-more">READ MORE &gt;&gt;</div>
</section>

<section class="section testimonials">
  <h2>Client Testimonials</h2>
  <div class="quote-badge"></div>
  <div class="quote-mark">&ldquo;</div>
  <div class="client-photo" role="img" aria-label="Portrait photo of the client"></div>
  <p class="quote-text">It is a long established fact that a reader will be distracted by the readable content of a page when looking at its layout. The point of using Lorem Ipsum is that it has a more-or-less normal distribution of letters, as opposed to using 'Content here, content here', making it look like readable English.</p>
  <div class="client-name">DANA WHITLEY</div>
  <div class="t-dots"><span></span><span></span><span></span></div>
</section>

<section class="section introducers">
  <h2>Our Introducers</h2>
  <svg class="carousel-arrow" style="left:100px" width="12" height="22" viewBox="0 0 12 22"><path d="M10 2L2 11L10 20" fill="none" stroke="#888" stroke-width="2"/></svg>
  <div class="partner" style="left:182px"><span></span></div>
  <div class="partner" style="left:352px"><span></span></div>
  <div class="partner" style="left:522px"><span></span></div>
  <div class="partner" style="left:692px"><span></span></div>
  <div class="partner" style="left:862px"><span></span></div>
  <svg class="carousel-arrow" style="left:1088px" width="12" height="22" viewBox="0 0 12 22"><path d="M2 2L10 11L2 20" fill="none" stroke="#888" stroke-width="2"/></svg>
</section>

<footer class="section site-footer">
  <div class="footer-brand"><span class="brand-mark"></span><span class="brand-name">Merrow Trade</span></div>
  <div class="footer-sub">TRADE FINANCE LIMITED</div>
  <div class="footer-col" style="left:425px">
    <h3>Information</h3>
    <ul class="footer-links"><li>Home</li><li>About us</li><li>Services</li><li>Introducers</li><li>Contact us</li></ul>
  </div>
  <div class="footer-col" style="left:598px">
    <h3>Newsletter</h3>
    <p class="news-text">Register your email address to get information about us</p>
    <div class="news-input">Email Address</div>
    <span class="news-btn">SUBSCRIBE</span>
  </div>
  <div class="footer-col" style="left:882px">
    <h3>Contact Us</h3>
    <div class="contact-row"><svg width="12" height="16" viewBox="0 0 12 16"><path d="M6 0A6 6 0 0 1 12 6C12 10 6 16 6 16S0 10 0 6A6 6 0 0 1 6 0Z" fill="#fff"/><circle cx="6" cy="6" r="2.2" fill="#1d1d1d"/></svg><span>Unit 4 Larchfield Court,<br>88 Kestrel Road, Bramwick, BW2 7QL</span></div>
    <div class="contact-row"><svg width="14" height="14" viewBox="0 0 14 14"><path d="M3 0L6 4L4 6Q6 9 8 10L10 8L14 11L12 14Q4 13 0 3Z" fill="#fff"/></svg><span>+44 1632 960 418</span></div>
    <div class="contact-row"><svg width="14" height="14" viewBox="0 0 14 14" fill="#fff"><rect x="3" y="0" width="8" height="5"/><rect x="0" y="5" width="14" height="9" rx="1"/></svg><span>+44 1632 960 772</span></div>
    <div class="contact-row"><svg width="14" height="12" viewBox="0 0 14 12"><rect width="14" height="12" rx="1" fill="#fff"/><path d="M0 1L7 7L14 1" fill="none" stroke="#1d1d1d" stroke-width="1.5"/></svg><span>info@merrowtradefinance.example</span></div>
  </div>
  <div class="footer-rule"></div>
  <div class="copyright">Copyrights © 2016, Merrow Trade finance. All rights reserved.</div>
  <div class="social"><span></span><span></span><span></span><span></span></div>
</footer>

</body>
</html>
```